Brightway Haus Inc. Business Card Design

Brightway Haus Inc. is in search of a great clean design for our business cards!

Looking to incorporate our full logo and watermark on side one (however, I am open to having the text and watermark separated within the design.)

On side two, I am looking to have contact information (Name, Position, Phone #, Email, Website (www.thebrightwayhaus.ca). Can have the logo and/or watermark as part of the design if applicable.

Please add tagline "Where Shine Counts" on either side 1 or 2. This tagline can be in a sans serif, serif or cursive font as long as it compliments overall design. Capitalization can be title or sentence case depending on how it fits within the design.

Get creative!! Looking for a clean, crisp, premium design! Looking for a glossy card finish with spot UV features when printed. Cards will also be printed with rounded corners. Standard dimensions (3.5 x 2).

Target Market(s)

B2B - primary clients are business owners or property management corporations. (residential jobs are few and far between)

Industry/Entity Type

Business

Contact Information for Business Card

- clean, crisp design
- double sided
- spot UV accents and glossy finish upon printing
- standard business card size (3.5 x 2) with rounded corners
- please see project description for requirements per side

Font styles to use
Sans Serif

Requirements
Must have
• - adequate bleeds with print ready files
• - cohesive design elements between side 1 & 2
• - spot UV elements (can be on both sides or just one, use your discretion)
• - colour pallet should match the logo file provided
• - incorporate tagline "where shine counts" (this tagline can be in a serif or sans serif font as long as it is complimentary to the overall design.
Nice to have
• - Premium elements with a clean design
Should not have
• - Please omit cartoon or whimsical like designs, think premium.
• - Colours should not stray from the pallet of the provided logo.

```html
<!DOCTYPE html>
<html lang="en">
<head>
<meta charset="utf-8">
<title>Brightway Haus Inc. Business Card</title>
<link rel="stylesheet" href="https://fonts.googleapis.com/css2?family=Open+Sans:wght@400;700&family=Roboto:wght@400;500;700&display=swap">
<style>
  :root {
    --bg: #d9d9db;
    --card: #2a2a2c;
    --card-edge: #1f1f21;
    --gloss: #3b3b3e;
    --teal: #17a9b4;
    --text-light: #d4d4d6;
    --text-mid: #a3a3a6;
  }
  * { margin: 0; padding: 0; box-sizing: border-box; }
  html, body { width: 799px; height: 1200px; overflow: hidden; }
  body {
    background: var(--bg);
    font-family: "Roboto", Arial, sans-serif;
    position: relative;
  }
  .card {
    position: absolute;
    left: 90px;
    width: 620px;
    height: 354px;
    background: var(--card);
    border-radius: 16px;
    overflow: hidden;
    box-shadow: 0 10px 24px rgba(0,0,0,0.25);
  }
  .card--front { top: 150px; }
  .card--back { top: 690px; }

  /* front: spot UV brand block */
  .front-brand {
    position: absolute;
    inset: 0;
    display: flex;
    align-items: center;
    justify-content: center;
    gap: 18px;
  }
  .front-brand__square {
    width: 64px;
    height: 64px;
    background: var(--gloss);
  }
  .front-brand__name {
    font-family: "Open Sans", Arial, sans-serif;
    font-weight: 700;
    font-size: 34px;
    letter-spacing: 1px;
    color: var(--gloss);
    text-transform: uppercase;
  }

  /* back: contact side */
  .accent-arc {
    position: absolute;
    left: -22px;
    top: 22px;
    width: 44px;
    height: 44px;
    border-radius: 50%;
    background: var(--teal);
  }
  .person {
    position: absolute;
    left: 44px;
    top: 26px;
  }
  .person__name {
    font-weight: 700;
    font-size: 24px;
    color: var(--teal);
  }
  .person__role {
    font-size: 12px;
    color: var(--text-mid);
    margin-top: 2px;
  }
  .contact {
    position: absolute;
    left: 26px;
    top: 160px;
    color: var(--text-light);
    font-size: 15px;
    line-height: 1.35;
  }
  .contact__address { margin-left: 26px; margin-bottom: 4px; }
  .contact__row { display: flex; align-items: center; gap: 10px; }
  .contact__icon { width: 16px; height: 16px; flex: none; }
  .contact__web-accent { color: var(--teal); }

  .wordmark {
    position: absolute;
    right: 34px;
    bottom: 36px;
    text-align: left;
  }
  .wordmark__line { display: flex; align-items: center; gap: 12px; }
  .wordmark__square { width: 26px; height: 26px; background: var(--teal); }
  .wordmark__name {
    font-family: "Open Sans", Arial, sans-serif;
    font-weight: 700;
    font-size: 32px;
    color: var(--teal);
    text-transform: uppercase;
    letter-spacing: -0.5px;
  }
  .wordmark__tagline {
    font-family: "Open Sans", Arial, sans-serif;
    font-size: 13px;
    letter-spacing: 5px;
    color: var(--text-mid);
    margin-top: 2px;
    margin-left: 40px;
  }
</style>
</head>
<body>
  <section class="card card--front" aria-label="Card front">
    <div class="front-brand">
      <div class="front-brand__square"></div>
      <div class="front-brand__name">Brightway Haus Inc.</div>
    </div>
  </section>

  <section class="card card--back" aria-label="Card back">
    <div class="accent-arc"></div>
    <div class="person">
      <div class="person__name">Daniel Reyes</div>
      <div class="person__role">Managing Director</div>
    </div>

    <div class="contact">
      <div class="contact__address">48 Harbour Lane, Suite 2,<br>Halifax NS</div>
      <div class="contact__row">
        <svg class="contact__icon" viewBox="0 0 16 16"><path fill="#17a9b4" d="M3 3h3l1 3-2 1c1 2 2 3 4 4l1-2 3 1v3c-6 0-10-4-10-10z"/></svg>
        <span>1800-555-0199</span>
      </div>
      <div class="contact__row">
        <svg class="contact__icon" viewBox="0 0 16 16"><rect x="1.5" y="3.5" width="13" height="9" fill="none" stroke="#17a9b4" stroke-width="1.5"/><path d="M1.5 3.5l6.5 5 6.5-5" fill="none" stroke="#17a9b4" stroke-width="1.5"/></svg>
        <span>dreyes@thebrightwayhaus.ca</span>
      </div>
      <div class="contact__row">
        <svg class="contact__icon" viewBox="0 0 16 16"><circle cx="8" cy="8" r="6.3" fill="none" stroke="#17a9b4" stroke-width="1.4"/><ellipse cx="8" cy="8" rx="2.6" ry="6.3" fill="none" stroke="#17a9b4" stroke-width="1.2"/><path d="M1.7 8h12.6" stroke="#17a9b4" stroke-width="1.2"/></svg>
        <span>www.<span class="contact__web-accent">thebrightwayhaus</span>.ca</span>
      </div>
    </div>

    <div class="wordmark">
      <div class="wordmark__line">
        <div class="wordmark__square"></div>
        <div class="wordmark__name">Brightway Haus Inc.</div>
      </div>
      <div class="wordmark__tagline">Where Shine Counts</div>
    </div>
  </section>
</body>
</html>
```